Robotic Physical Therapy office needs a Grand Opening Flyer

We need a Grand Opening flyer design for a robotic physical therapy office named Kinetic Harbor Wellness. We would like it to have a clean, classy, upscale feeling that gives potential clients a V.I.P. feeling. We would like to use the colors black, gray, and yellow (logo will be uploaded).

Event: Thursday, June 1st, 2023 from 12pm-6pm
location: 58274 Pellham Ave, Bloomfield Hills, MI 48519

Industry/Entity Type

Physical therapy

Font styles to use
Script

Colors

Designer to choose colors to be used in the design.

Requirements
Nice to have
• More of a vip feel for the invite

```html
<!DOCTYPE html>
<html lang="en">
<head>
<meta charset="UTF-8">
<title>Kinetic Harbor Wellness – Grand Opening</title>
<link rel="stylesheet" href="https://fonts.googleapis.com/css2?family=Poppins:wght@300;400;500;600&family=Abhaya+Libre:wght@500&display=swap">
<style>
  :root {
    --page-bg: #eceef1;
    --flyer-dark: #1c1b29;
    --flyer-mid: #25253a;
    --gold: #f3d52a;
    --white: #ffffff;
    --ring: #6e6883;
    --photo-green: #5e8a70;
    --photo-light: #d9d6d0;
  }
  * { margin: 0; padding: 0; box-sizing: border-box; }
  html, body { width: 691px; height: 1200px; overflow: hidden; }
  body {
    background: var(--page-bg);
    font-family: "Poppins", sans-serif;
    position: relative;
  }
  .flyer {
    position: absolute;
    left: 26px; top: 186px;
    width: 640px; height: 828px;
    background: linear-gradient(160deg, var(--flyer-mid) 0%, var(--flyer-dark) 55%, #181726 100%);
    overflow: hidden;
    box-shadow: 0 6px 18px rgba(0,0,0,0.25);
  }
  .top-rule {
    position: absolute; left: 0; top: 0;
    width: 300px; height: 3px; background: var(--gold);
  }
  .hero-art { position: absolute; left: 0; top: 0; width: 640px; height: 340px; }
  .brand {
    position: absolute; left: 44px; top: 108px;
    display: flex; align-items: center; gap: 10px;
  }
  .brand-dot {
    width: 34px; height: 34px; border-radius: 50%;
    border: 3px solid var(--white);
  }
  .brand-name {
    color: var(--white); font-weight: 600; font-size: 19px; line-height: 1.1;
    width: 160px;
  }
  .title-grand {
    position: absolute; left: 53px; top: 266px;
    color: var(--gold); font-weight: 600; font-size: 86px; line-height: 1;
    letter-spacing: 1px; white-space: nowrap;
  }
  .title-opening {
    position: absolute; left: 52px; top: 326px;
    color: var(--white); font-family: "Abhaya Libre", serif; font-weight: 500;
    font-size: 118px; line-height: 1; letter-spacing: 3px; white-space: nowrap;
  }
  .service-box {
    position: absolute; left: 51px; top: 435px;
    width: 516px; height: 57px;
    border: 1.5px solid var(--gold);
    display: flex; align-items: center; justify-content: center;
    font-size: 32px; letter-spacing: 1px; color: var(--white); font-weight: 400;
    white-space: nowrap;
  }
  .service-box .accent { color: var(--gold); font-weight: 300; margin-right: 10px; }
  .date-row {
    position: absolute; left: 55px; top: 562px;
    display: flex; gap: 15px; white-space: nowrap;
  }
  .date-part {
    border-top: 2px dotted var(--white);
    border-bottom: 2px dotted var(--white);
    font-size: 38px; line-height: 57px; height: 61px;
    white-space: nowrap;
  }
  .date-day { color: var(--white); font-weight: 300; letter-spacing: 0.5px; }
  .date-month { color: var(--gold); font-weight: 500; border-color: var(--gold); }
  .year {
    position: absolute; left: 53px; top: 640px;
    color: var(--white); font-weight: 600; font-size: 54px; line-height: 1;
    z-index: 2; white-space: nowrap;
  }
  .time-bar {
    position: absolute; left: 192px; top: 650px;
    width: 252px; height: 42px; background: var(--gold);
    color: var(--flyer-dark); font-weight: 500; font-size: 26px;
    line-height: 42px; padding-left: 16px; white-space: nowrap;
  }
  .address {
    position: absolute; left: 55px; top: 744px;
    display: flex; align-items: center; gap: 10px;
    color: var(--white); font-weight: 300; font-size: 18px; white-space: nowrap;
  }
  .address-rule {
    position: absolute; left: 55px; top: 789px;
    width: 585px; height: 1px; background: var(--gold);
  }
</style>
</head>
<body>
  <main class="flyer">
    <div class="top-rule"></div>

    <svg class="hero-art" viewBox="0 0 640 340">
      <defs>
        <linearGradient id="photoTone" x1="0" y1="0" x2="1" y2="1">
          <stop offset="0" stop-color="#5e8a70"/>
          <stop offset="0.55" stop-color="#d9d6d0"/>
          <stop offset="1" stop-color="#4d7560"/>
        </linearGradient>
        <clipPath id="heroClip"><rect width="640" height="340"/></clipPath>
      </defs>
      <g clip-path="url(#heroClip)">
        <circle cx="652" cy="-26" r="356" fill="#6e6883"/>
        <circle cx="652" cy="-26" r="348" fill="#d8d6e0"/>
        <circle cx="652" cy="-26" r="343" fill="url(#photoTone)" role="img"
                aria-label="Photo: a therapist guiding a patient through an arm-stretch exercise in a green-walled clinic room"/>
      </g>
    </svg>

    <div class="brand">
      <span class="brand-dot"></span>
      <span class="brand-name">KINETIC HARBOR WELLNESS</span>
    </div>

    <h1 class="title-grand">GRAND</h1>
    <div class="title-opening">OPENING</div>

    <div class="service-box"><span class="accent">ROBOTIC</span>PHYSICAL THERAPY</div>

    <div class="date-row">
      <div class="date-part date-day">THURSDAY</div>
      <div class="date-part date-month">JUNE 1ST</div>
    </div>

    <div class="time-bar">from 12pm-6pm</div>
    <div class="year">2023</div>

    <div class="address">
      <svg width="26" height="38" viewBox="0 0 26 38" fill="none" stroke="#f3d52a" stroke-width="1.8">
        <path d="M13 34C13 34 3 21 3 13a10 10 0 0 1 20 0c0 8-10 21-10 21z"/>
        <circle cx="13" cy="13" r="4"/>
        <ellipse cx="13" cy="35" rx="6" ry="1.6"/>
      </svg>
      <span>58274 Pellham Ave, Bloomfield Hills, MI 48519</span>
    </div>
    <div class="address-rule"></div>
  </main>
</body>
</html>
```